Business Card design for insurance broker in Denver, CO, USA

I need a business card designed using this logo that was just created. We sell life and disability income insurance to US consumers.
Looking for a professionally designed card to make use of the logo and have something to hand to prospects or new business referral sources. The card could be white, gray, black or whatever you would recommend.

Target Market(s)

US Consumers and other financial professionals that I partner with.

Industry/Entity Type

Insurance Broker

Contact Information for Business Card

Owen T. Farrow, CLU, LUTCF (please note that CLU should have a superscript R in a circle for registered trademark)
President
phone (303) 555-0187
email owen@keelbrookcover.example
4620 W. Halvern Rd, Suite 300, Alder Glen, CO 80427
Somewhere fit in a tagline saying "Your resource for life, long term care, and disability insurance" (maybe the back if it doesn't fit on the front, your call)

Font styles to use
Sans Serif

Requirements
Must have
• Must have logo in correct blue and gray colors, my name, address, phone, email. Order and placement determined by the designer.
• I just want something that looks a more professional than what I could have done using the business card designer tool on pixelbazaar.example or QuillPress, or any other do-it-yourself tool
• A regular rectangular business card with square corners is preferred
Nice to have
• I included the logos of 2 organizations I belong to (GKLS and WOBCE). They should be small, but visible on the back only. If it doesn’t look good, this is not a requirement, feel free to drop it.
Should not have
• Do not add any colors not already in the logo, except use of black and whites which are okay. If you use the logo on the back and want to make that in all black, gray or white, that may be okay as well.

```html
<!DOCTYPE html>
<html lang="en">
<head>
<meta charset="utf-8">
<title>Keelbrook Insurance Solutions – Business Card</title>
<link href="https://fonts.googleapis.com/css2?family=Montserrat:wght@500;600;700&display=swap" rel="stylesheet">
<style>
  :root {
    --brand-blue: #1b7ec2;
    --brand-gray: #7d7f82;
    --paper: #f4f5f6;
    --ink: #55585c;
    --backdrop: #aab6c8;
    --badge: rgba(255,255,255,0.22);
  }
  * { box-sizing: border-box; margin: 0; padding: 0; }
  html, body { width: 1200px; height: 675px; overflow: hidden; }
  body {
    background: var(--backdrop);
    font-family: "Montserrat", Arial, sans-serif;
    position: relative;
  }
  .card {
    position: absolute;
    top: 190px;
    width: 525px;
    height: 300px;
    box-shadow: 0 10px 24px rgba(40,55,80,0.25);
    overflow: hidden;
  }
  .card-front { left: 50px; background: var(--paper); }
  .card-back { left: 625px; background: var(--brand-blue); }

  .brand-name {
    position: absolute;
    font-weight: 700;
    letter-spacing: 0.04em;
    line-height: 1.1;
    text-transform: uppercase;
    white-space: nowrap;
  }
  .card-front .brand-name {
    top: 40px; left: 0; right: 0;
    text-align: center;
    color: var(--brand-blue);
    font-size: 18px;
  }
  .card-back .brand-name {
    top: 110px; left: 60px;
    color: #fff;
    font-size: 26px;
  }

  .title {
    position: absolute;
    right: 28px; top: 106px;
    color: var(--brand-blue);
    font-weight: 700;
    font-size: 11px;
    letter-spacing: 0.28em;
  }
  .rule {
    position: absolute;
    left: 28px; right: 28px; top: 124px;
    height: 2px;
    background: var(--brand-blue);
  }
  .address {
    position: absolute;
    right: 28px; top: 132px;
    display: flex; gap: 6px;
    color: var(--ink);
    font-size: 8.5px;
    font-weight: 500;
    line-height: 1.35;
  }
  .name {
    position: absolute;
    left: 28px; top: 100px;
    color: var(--brand-blue);
    font-size: 15px;
    font-weight: 700;
  }
  .name .cred { color: var(--brand-gray); font-weight: 600; }
  .name sup { font-size: 8px; }
  .contact-list {
    position: absolute;
    left: 28px; top: 140px;
    list-style: none;
    color: var(--ink);
    font-size: 9.5px;
    font-weight: 500;
  }
  .contact-list li { display: flex; align-items: center; gap: 8px; margin-bottom: 7px; }
  .contact-list svg { width: 10px; height: 10px; fill: var(--brand-blue); flex: none; }
  .tagline-band {
    position: absolute;
    left: 0; right: 0; bottom: 0;
    height: 84px;
    background: var(--brand-blue);
    display: flex; align-items: center; justify-content: center;
    text-align: center;
    color: #fff;
    font-weight: 700;
    font-size: 12.5px;
    letter-spacing: 0.12em;
    line-height: 1.4;
    text-transform: uppercase;
  }

  .badge { position: absolute; background: var(--badge); border-radius: 6px; width: 72px; height: 48px; right: 40px; }
  .badge-wobce { top: 36px; }
  .badge-gkls { top: 200px; }
</style>
</head>
<body>

<section class="card card-front" aria-label="Business card front">
  <p class="brand-name">Keelbrook Insurance Solutions</p>

  <p class="name">Owen T. Farrow, <span class="cred">CLU<sup>®</sup>, LUTCF</span></p>
  <p class="title">PRESIDENT</p>
  <div class="rule"></div>
  <div class="address">
    <svg viewBox="0 0 10 12" width="9" height="11" fill="var(--brand-blue)"><path d="M5 0a4 4 0 0 0-4 4c0 3 4 8 4 8s4-5 4-8a4 4 0 0 0-4-4zm0 5.5A1.5 1.5 0 1 1 5 2.5a1.5 1.5 0 0 1 0 3z"/></svg>
    <span>4620 W. Halvern Rd, Suite 300,<br>Alder Glen, CO 80427</span>
  </div>

  <ul class="contact-list">
    <li><svg viewBox="0 0 10 10"><path d="M2 0l2 2-1 1.5c.6 1.3 1.7 2.4 3 3L7.5 5.5l2 2L8 9.5C4 9.5.5 6 .5 2z"/></svg>(303) 555-0187</li>
    <li><svg viewBox="0 0 10 10"><path d="M0 2h10v6H0zm1 1l4 3 4-3v-.2H1z"/></svg>owen@keelbrookcover.example</li>
    <li><svg viewBox="0 0 10 10"><circle cx="5" cy="5" r="5"/></svg>www.keelbrookcover.example</li>
  </ul>

  <div class="tagline-band">Your resource for life, long term care,<br>and disability insurance</div>
</section>

<section class="card card-back" aria-label="Business card back">
  <p class="brand-name">Keelbrook<br>Insurance Solutions</p>
  <div class="badge badge-wobce" role="img" aria-label="WOBCE membership badge"></div>
  <div class="badge badge-gkls" role="img" aria-label="GKLS membership badge"></div>
</section>

</body>
</html>
```